Meridian Vault Data Works Needs a Website Desing

We need a website design for a new company based in Kuwait called Meridian Vault Data Works (MVDW). We provide Software as a Service (SaaS) solutions for small and medium business companies. We will develop the required E-systems like HR,Payroll,Accounting Systems for those customers who wants to focus on their business instead of wasting time to automate it. MVDW need a web site that represent this activity and showing our cloud products and allow out customers to easily identify their needs. as a normal web site basic things need to be included like :
about MVDW
Solutions
PressRoom
Contact us
please i need something similar to tralvex.com or ozk.com or www.plorvane.com with blue and black theme .. please check the Company's logo
hi all ,,,
the project is only design without any codes
Reason: The project is focus on design only ,, i will be really appreciated to have more designs

```html
<!DOCTYPE html>
<html lang="en">
<head>
<meta charset="utf-8">
<title>Meridian Vault Data Works</title>
<link rel="stylesheet" href="https://fonts.googleapis.com/css2?family=Open+Sans:wght@400;600;700&family=Pathway+Gothic+One&display=swap">
<style>
:root{
  --ink:#111;
  --text:#444;
  --blue:#1f56a8;
  --nav-blue:#1e4fb6;
  --heading-blue:#1d4f86;
  --service-blue:#2a62a8;
  --hero-deep:#1c3f94;
  --hero-light:#5f8fd0;
  --footer:#2453a9;
  --footer-dark:#1d3f8d;
  --link-red:#a4141a;
  --button:#1f5e96;
  --go:#5aa6e6;
  --panel:#fff;
  --page:#ececec;
}
*{box-sizing:border-box;margin:0;padding:0}
html,body{width:1200px;height:1192px;overflow:hidden}
body{position:relative;background:var(--page);font-family:"Open Sans",sans-serif;color:var(--text)}
.abs{position:absolute}
.topbar{left:0;top:0;width:1200px;height:45px;background:linear-gradient(#5a5a5a,#2a2a2a 60%,#1a1a1a)}
.search{left:790px;top:7px;width:221px;height:24px;border-radius:12px;background:#1b1b1b;border:1px solid #777;color:#888;font-style:italic;font-size:13px;padding:3px 12px}
.search svg{position:absolute;right:9px;top:5px}
.header{left:0;top:45px;width:1200px;height:103px;background:#fff}
.brand-mark{left:145px;top:57px;width:78px;height:78px;border-radius:50%;background:#2b8fd8}
.brand-name{left:232px;top:56px;font-size:54px;font-weight:700;color:var(--ink);letter-spacing:1px;line-height:1}
.brand-full{left:234px;top:116px;font-size:12px;font-weight:700;color:var(--ink);line-height:1}
.phone{left:803px;top:70px}
.phone-number{left:845px;top:66px;font-size:26px;color:var(--blue)}
.nav a{position:absolute;top:113px;height:33px;line-height:33px;text-align:center;color:#fff;font-size:13px;text-decoration:none;background:linear-gradient(#2f63c8,var(--nav-blue))}
.nav a.active{background:#0d0d0d}
.hero{left:0;top:148px;width:1200px;height:362px;background:radial-gradient(ellipse at 80% 10%,var(--hero-light),var(--hero-deep) 70%)}
.hero-art{left:150px;top:160px;width:490px;height:340px;border-radius:40px;background:radial-gradient(ellipse at center,rgba(255,255,255,.55),rgba(120,190,240,.15) 70%,transparent)}
.hero-arrow{top:300px;width:36px;height:36px;border-radius:50%;background:#1a4a8a;border:2px solid #5d8bc6}
.hero-arrow svg{position:absolute;left:12px;top:10px}
.hero-title{left:683px;top:240px;font-size:21px;color:#fff;letter-spacing:.3px}
.hero-rule{left:683px;top:276px;width:322px;height:1px;background:rgba(255,255,255,.35)}
.hero-copy{left:682px;top:295px;width:345px;font-size:13px;line-height:21px;color:#e6eefa}
.backdrop{left:0;top:510px;width:1200px;height:506px;background:linear-gradient(90deg,#e6e6e6,#fafafa 10%,#fafafa 90%,#e6e6e6)}
.panel{left:128px;top:510px;width:944px;height:506px;background:var(--panel);border-left:1px solid #ccc;border-right:1px solid #ccc}
.heading{font-family:"Pathway Gothic One",sans-serif;font-size:24px;line-height:1;color:var(--ink)}
.heading .tint{color:var(--heading-blue)}
.card{top:576px;width:287px;height:153px;border:1px solid #ddd;border-radius:3px;background:linear-gradient(#fff,#f5f5f5);box-shadow:0 3px 4px rgba(0,0,0,.06)}
.card-art{position:absolute;left:10px;top:28px;width:75px;height:78px;border-radius:8px}
.card-title{position:absolute;left:98px;top:20px;font-family:"Pathway Gothic One",sans-serif;font-size:22px;color:var(--service-blue);white-space:nowrap}
.card-copy{position:absolute;left:98px;top:51px;width:185px;font-size:11px;line-height:16px;color:#555}
.card-more{position:absolute;left:103px;top:108px;font-size:11px;color:var(--link-red)}
.welcome-lead{left:156px;top:828px;font-size:12px;font-weight:700;color:var(--ink)}
.welcome-copy{left:157px;top:851px;width:572px;font-size:11px;line-height:18px;color:#555}
.button{left:642px;top:938px;width:81px;height:32px;background:var(--button);color:#fff;font-family:"Pathway Gothic One",sans-serif;font-size:17px;line-height:32px;text-align:center}
.welcome-art{left:765px;top:785px;width:290px;height:190px;border-radius:60px;background:radial-gradient(ellipse at center,#cfe6fb,#7ab7ea 60%,rgba(255,255,255,0) 75%)}
.footer{left:0;top:1016px;width:1200px;height:176px;background:linear-gradient(var(--footer),var(--footer-dark))}
.footer .heading{color:#fff;font-size:19px}
.email{left:120px;top:1086px;width:283px;height:24px;background:#fff;border:1px solid #b8c6e0;font-size:12px;color:#777;padding:3px 8px}
.go{left:354px;top:1130px;width:49px;height:24px;background:var(--go);color:#fff;font-size:13px;text-align:center;line-height:24px;border:1px solid #8fc6f2}
.news{color:#dfe8f8;font-size:11px;line-height:16px}
.social{top:1042px;width:20px;height:20px;border-radius:2px;background:#4a86d4}
.footer-links{right:122px;top:1082px;font-size:11px;color:#fff;text-align:right}
.footer-copy{right:121px;top:1109px;font-size:11px;color:#e6edf8}
</style>
</head>
<body>
<div class="abs topbar"></div>
<div class="abs search">Search
  <svg width="13" height="13" viewBox="0 0 13 13"><circle cx="5" cy="5" r="4" fill="none" stroke="#ccc" stroke-width="2"/><line x1="8" y1="8" x2="12" y2="12" stroke="#ccc" stroke-width="2"/></svg>
</div>

<header>
  <div class="abs header"></div>
  <div class="abs brand-mark"></div>
  <div class="abs brand-name">MVDW</div>
  <div class="abs brand-full">Meridian Vault Data Works</div>
  <svg class="abs phone" width="30" height="26" viewBox="0 0 30 26"><path d="M6 2c-3 1-5 4-3 8 3 6 9 12 15 14 4 1 7-1 8-3l-5-4-3 2c-3-1-6-4-7-7l2-3z" fill="#555"/></svg>
  <div class="abs phone-number">(965) 2240-7718</div>
  <nav class="nav">
    <a class="active" style="left:520px;width:91px">HOME</a>
    <a style="left:614px;width:116px">ABOUT &nbsp;MVDW</a>
    <a style="left:733px;width:101px">SOLUTIONS</a>
    <a style="left:837px;width:101px">PRESSROOM</a>
    <a style="left:941px;width:102px">CONTACT US</a>
  </nav>
</header>

<section>
  <div class="abs hero"></div>
  <div class="abs hero-art" role="img" aria-label="Cloud server connected to desktops, laptops, tablets and phones"></div>
  <div class="abs hero-arrow" style="left:50px"><svg width="10" height="14" viewBox="0 0 10 14"><path d="M8 2L3 7l5 5" fill="none" stroke="#fff" stroke-width="2.5"/></svg></div>
  <div class="abs hero-arrow" style="left:1101px"><svg width="10" height="14" viewBox="0 0 10 14"><path d="M2 2l5 5-5 5" fill="none" stroke="#fff" stroke-width="2.5"/></svg></div>
  <h1 class="abs hero-title" style="font-weight:400">LOREM IPSUM DOLOR SIT AMET, ELIT</h1>
  <div class="abs hero-rule"></div>
  <p class="abs hero-copy">Cum sociis natoque penatibus et magnis dis parturient montes, nascetur ridiculus mus. In iaculis facilisis massa. Etiam eu urna. Sed porta.Cum sociis natoque penatibus et magnis dis parturient montes, nascetur ridiculus mus.</p>
</section>

<main>
  <div class="abs backdrop"></div>
  <div class="abs panel"></div>
  <h2 class="abs heading" style="left:156px;top:528px;font-weight:400"><span class="tint">OUR</span>&nbsp; SERVICES</h2>

  <article class="abs card" style="left:145px">
    <div class="card-art" role="img" aria-label="Bar chart figure" style="background:linear-gradient(#bcd6f2,#3c7bd0)"></div>
    <h3 class="card-title" style="font-weight:400">BUSINESS CONSULTANCY</h3>
    <p class="card-copy">Nunc varius facilisis eros. Sed erat. In in velit &nbsp;quis arcu ornare laoreet. Nunc varius facilisis eros. Sed erat.</p>
    <span class="card-more">View More &nbsp;&gt;&gt;</span>
  </article>
  <article class="abs card" style="left:456px">
    <div class="card-art" role="img" aria-label="Globe with wrench" style="background:radial-gradient(circle,#4c8fe0,#1e4f9e 55%,transparent 70%)"></div>
    <h3 class="card-title" style="font-weight:400">MANAGED SERVICES</h3>
    <p class="card-copy">Nunc varius facilisis eros. Sed erat. In in velit &nbsp;quis arcu ornare laoreet. Nunc varius facilisis eros. Sed erat.</p>
    <span class="card-more">View More &nbsp;&gt;&gt;</span>
  </article>
  <article class="abs card" style="left:767px">
    <div class="card-art" role="img" aria-label="Computer monitor" style="background:linear-gradient(#2a6cc8,#0d2f6a)"></div>
    <h3 class="card-title" style="font-weight:400">CLOUD COMPUTER SERVICES</h3>
    <p class="card-copy">Nunc varius facilisis eros. Sed erat. In in velit &nbsp;quis arcu ornare laoreet. Nunc varius facilisis eros. Sed erat.</p>
    <span class="card-more">View More &nbsp;&gt;&gt;</span>
  </article>

  <h2 class="abs heading" style="left:156px;top:787px;font-weight:400"><span class="tint">WELCOME TO</span> MVDW</h2>
  <p class="abs welcome-lead">Mauris vel lacus vitae felis vestibulum volutpat. Etiam est nunc, venisl.</p>
  <p class="abs welcome-copy">Sed ut perspiciatis unde omnis iste natus error sit voluptatem accusantium doloremque laudantium, totam rem aperiam, eaque ipsa quae ab illo inventore veritatis et quasi architecto beatae vitae dicta sunt explicabo. Nemo enim ipsam voluptatem quia voluptas sit aspernatur aut odit aut fugit, sed quia consequuntur magni dolores eos qui ratione voluptatem sequi nesciunt. Neque porro quisquam est, qui dolorem ipsum quia dolor sit amet.</p>
  <div class="abs button">learn more</div>
  <div class="abs welcome-art" role="img" aria-label="Laptop surrounded by blue clouds"></div>
</main>

<footer>
  <div class="abs footer"></div>
  <h4 class="abs heading" style="left:122px;top:1044px;font-weight:400">NEWSLETTER SIGN UP</h4>
  <div class="abs email">Your email address</div>
  <div class="abs go">GO</div>

  <h4 class="abs heading" style="left:463px;top:1044px;font-weight:400">LATEST NEWS</h4>
  <p class="abs news" style="left:462px;top:1080px">apr 30, 2013</p>
  <p class="abs news" style="left:462px;top:1096px;width:262px">Sed ut perspiciatis unde omnis iste natus error sit voluptatem accusantium doloremque laudantium, totam rem aperiam, eaque ipsa quae ab illo inven.</p>
  <p class="abs news" style="left:658px;top:1151px;color:#fff">More &nbsp;&gt;&gt;</p>

  <div class="abs social" style="left:969px" aria-label="Social link"></div>
  <div class="abs social" style="left:997px" aria-label="Social link"></div>
  <div class="abs social" style="left:1023px" aria-label="News feed"></div>
  <div class="abs social" style="left:1050px" aria-label="Social link"></div>

  <p class="abs footer-links">Home &nbsp;| &nbsp;About MVDW &nbsp;| &nbsp;Solutions &nbsp;| &nbsp;PressRoom &nbsp;| &nbsp;Contact us</p>
  <p class="abs footer-copy">© 2013 MVDW, All Rights Reserved</p>
</footer>
</body>
</html>
```